I need a fresh looking, exciting and loaded design for Full service Restaurant

We need a web design for our restaurant, which offers full service Pakistani and Indian food in PA, USA. Design should be elegant, simplified so customers can navigate easily and order food online for catering as well as delivery. We need loads of pictures and room to grow. I already have a web address via vemrilo.com. It should include SSL and e-commerce for ordering food.
Be original and be creative and make it a fun site :)

```html
<!DOCTYPE html>
<html lang="en">
<head>
<meta charset="utf-8">
<title>Saffron Lane – A fine Pak-Indian Cuisine</title>
<link rel="stylesheet" href="https://fonts.googleapis.com/css2?family=Open+Sans:wght@400;600;700;800&family=Great+Vibes&display=swap">
<style>
:root{
  --red:#d91f1f;
  --red-dark:#b51414;
  --green:#1f5a0c;
  --green-dark:#184a08;
  --white:#ffffff;
  --ink:#333333;
  --muted:#666666;
  --line:#dddddd;
  --gold:#f2c200;
  --price-red:#c8101a;
}
*{margin:0;padding:0;box-sizing:border-box}
html,body{width:1200px;height:2390px;overflow:hidden;background:var(--white)}
body{font-family:"Open Sans",Arial,sans-serif;color:var(--ink)}
.page{position:relative;width:1200px;height:2390px;overflow:hidden}
.abs{position:absolute}
.script{font-family:"Great Vibes",cursive;font-weight:400}

/* hero */
.hero{left:0;top:0;width:1200px;height:570px;
  background:radial-gradient(ellipse at 20% 40%,#c99a3c 0,#b9862f 18%,transparent 40%),
             radial-gradient(ellipse at 75% 45%,#f3efe6 0,#e6e1d4 30%,transparent 60%),
             linear-gradient(90deg,#a9843f 0,#d8c9a4 35%,#ebe6da 60%,#c8c3b2 100%)}
.hero-veil{left:0;top:0;width:1200px;height:570px;background:rgba(0,0,0,.12)}
.brand{left:0;top:70px;width:1200px;text-align:center}
.brand-name{font-size:56px;font-weight:700;color:var(--red);line-height:1}
.brand-tag{font-size:20px;font-weight:600;color:var(--green);margin-top:8px}
.icon-btn{top:62px;width:40px;height:40px;background:var(--white);border-radius:4px;display:flex;align-items:center;justify-content:center;box-shadow:0 1px 3px rgba(0,0,0,.15)}
.hero-arrow{top:268px}
.hero-title{left:0;top:310px;width:1200px;text-align:center;font-size:56px;font-weight:800;letter-spacing:6px;color:var(--white);text-shadow:0 2px 6px rgba(0,0,0,.45)}
.hero-sub{left:0;top:384px;width:1200px;text-align:center;font-size:20px;font-weight:600;color:var(--white);text-shadow:0 1px 4px rgba(0,0,0,.5)}

/* navigation */
.nav{left:0;top:570px;width:1200px;height:52px;background:var(--red);border-bottom:5px solid var(--red-dark)}
.nav-mark{left:246px;top:9px;width:30px;height:30px;border-radius:50%;background:var(--white)}
.nav-item{top:16px;font-size:12px;font-weight:600;color:var(--white);text-transform:uppercase}
.nav-item.is-active{font-size:14px;font-weight:700;top:14px}
.nav-sep{top:15px;font-size:13px;color:var(--white)}

/* why choose */
.why-photo{left:120px;top:675px;width:448px;height:288px;border:6px solid #c4c4c4;border-radius:6px;
  background:linear-gradient(135deg,#c8a06a 0,#8a4a2a 45%,#c83a2a 60%,#e9e2d4 100%)}
.section-title{color:var(--green);font-size:44px}
.why-title{left:608px;top:668px;width:468px;text-align:center}
.why-text{left:608px;top:750px;width:468px;font-size:13px;line-height:22px;color:var(--ink);text-align:justify;text-align-last:center}
.btn-outline{left:773px;top:898px;width:104px;height:44px;border:1px solid var(--line);font-size:13px;color:var(--ink);display:flex;align-items:center;justify-content:center;background:var(--white)}

/* services */
.service{left:0;top:1008px;width:1200px;height:434px;background:linear-gradient(90deg,#2a5a08 0,#6a4010 40%,#b52a14 70%,#d21f1a 100%)}
.service-title{left:0;top:40px;width:1200px;text-align:center;color:var(--white);font-size:46px}
.service-sub{left:0;top:112px;width:1200px;text-align:center;color:var(--white);font-size:11px;font-weight:600;text-transform:uppercase}
.dish-circle{width:208px;height:208px;border-radius:50%;border:4px solid var(--white);display:flex;align-items:center;justify-content:center;top:163px}
.dish-circle span{color:var(--white);font-size:28px;text-shadow:0 1px 3px rgba(0,0,0,.6)}
.dish-pak{left:341px;background:linear-gradient(135deg,#d9cfbf,#a48a62 60%,#6e5a3c)}
.dish-ind{left:652px;background:linear-gradient(135deg,#a8b66a,#d8a848 50%,#6e6a3a)}

/* products */
.products-title{left:0;top:1475px;width:1200px;text-align:center}
.tab{top:1572px;width:106px;height:38px;border:1px solid var(--line);font-size:12px;color:var(--green);display:flex;align-items:center;justify-content:center;background:var(--white)}
.tab.is-active{background:var(--green);color:var(--white);border-color:var(--green)}
.product-photo{top:1650px;width:297px;height:326px;box-shadow:0 2px 4px rgba(0,0,0,.2)}
.photo-salad{left:120px;background:linear-gradient(160deg,#6f9a34,#c7281e 45%,#e9e6dc 75%,#2a2a2a)}
.photo-nacho{left:453px;background:linear-gradient(160deg,#3a2a1c,#d89a2a 40%,#8aa83a 55%,#b83018)}
.photo-rice{left:785px;background:linear-gradient(160deg,#8a4a2a,#e3b84a 40%,#d89a2a 70%,#6a3a1a)}
.cart-chip{left:126px;top:222px;width:44px;height:38px;background:var(--green);display:flex;align-items:center;justify-content:center}
.price{left:0;top:272px;width:297px;text-align:center;color:var(--white);font-size:17px}
.price s{margin-right:6px}
.product-name{top:1996px;width:297px;text-align:center;font-size:15px;font-weight:600;color:var(--price-red)}
.stars{top:2022px;width:297px;text-align:center;color:var(--gold);font-size:13px;letter-spacing:4px}
.pager{top:2084px;width:28px;height:28px;border-radius:50%;background:#e4e4e4;display:flex;align-items:center;justify-content:center}

/* footer */
.footer{left:0;top:2196px;width:1200px;height:194px;background:linear-gradient(90deg,#1f5a08 0,#6a3a10 45%,#c2241a 75%,#dc1f1c 100%);clip-path:polygon(0 0,100% 10px,100% 100%,0 100%)}
.footer-badge{left:556px;top:2152px;width:88px;height:88px;border-radius:50%;background:var(--green);border:4px solid var(--white);display:flex;align-items:center;justify-content:center;color:var(--white);font-size:11px;font-weight:700;text-align:center;line-height:1.2}
.social{top:2256px;width:34px;height:34px;border-radius:50%;border:2px solid var(--white)}
.footer-links{left:0;top:2303px;width:1200px;text-align:center;color:var(--white);font-size:12px}
.footer-copy{left:0;top:2334px;width:1200px;text-align:center;color:var(--white);font-size:12px}
</style>
</head>
<body>
<div class="page">

  <!-- hero -->
  <div class="abs hero" role="img" aria-label="Photo of yellow lentil dal in a copper bowl beside white rice with coriander and a serving spoon"></div>
  <div class="abs hero-veil"></div>
  <div class="abs brand">
    <div class="brand-name">Saffron Lane</div>
    <div class="brand-tag">A fine Pak-Indian Cuisine</div>
  </div>
  <div class="abs icon-btn" style="left:988px">
    <svg width="16" height="15" viewBox="0 0 16 15"><path d="M0 1h3l2 8h8l2-6H4.5" fill="none" stroke="#d91f1f" stroke-width="2"/><circle cx="6" cy="12.5" r="1.5" fill="#d91f1f"/><circle cx="12" cy="12.5" r="1.5" fill="#d91f1f"/></svg>
  </div>
  <div class="abs icon-btn" style="left:1058px">
    <svg width="16" height="16" viewBox="0 0 16 16"><circle cx="6.5" cy="6.5" r="4.5" fill="none" stroke="#d91f1f" stroke-width="2.2"/><path d="M10 10l5 5" stroke="#d91f1f" stroke-width="2.4"/></svg>
  </div>
  <svg class="abs hero-arrow" style="left:34px" width="20" height="86" viewBox="0 0 20 86"><path d="M18 2L3 43l15 41" fill="none" stroke="#d91f1f" stroke-width="2"/></svg>
  <svg class="abs hero-arrow" style="left:1146px" width="20" height="86" viewBox="0 0 20 86"><path d="M2 2l15 41L2 84" fill="none" stroke="#d91f1f" stroke-width="2"/></svg>
  <div class="abs hero-title">WELCOME TO</div>
  <div class="abs hero-sub">We offer full service Pakistani and Indian food in Philadelphia, USA</div>

  <!-- navigation -->
  <nav class="abs nav">
    <div class="abs nav-mark"></div>
    <div class="abs nav-item is-active" style="left:292px">Home</div>
    <div class="abs nav-sep" style="left:374px">/</div>
    <div class="abs nav-item" style="left:424px">About Us</div>
    <div class="abs nav-sep" style="left:524px">/</div>
    <div class="abs nav-item" style="left:574px">Services</div>
    <div class="abs nav-sep" style="left:668px">/</div>
    <div class="abs nav-item" style="left:717px">Features</div>
    <div class="abs nav-sep" style="left:820px">/</div>
    <div class="abs nav-item" style="left:865px">Contacts</div>
  </nav>

  <!-- why choose us -->
  <div class="abs why-photo" role="img" aria-label="Photo of grilled chapli kebabs topped with tomato slices on a plate with salad and green chutney"></div>
  <h2 class="abs section-title script why-title">Why Choose Us?</h2>
  <p class="abs why-text">Lorem Ipsum is simply dummy text of the printing and typesetting industry. Lorem Ipsum has been the industry's standard dummy text ever since the 1500s, when an unknown printer took a galley of type and scrambled it to make a type specimen book. It has survived not only five centuries, but also the leap into electronic typesetting, remaining essentially unchanged.</p>
  <div class="abs btn-outline">LEARN MORE</div>

  <!-- services -->
  <section class="abs service" role="img" aria-label="City skyline and bridge photo tinted from green to red">
    <h2 class="abs script service-title">Our Service</h2>
    <div class="abs service-sub">We offer full service Pakistani and Indian food in Philadelphia, USA</div>
    <div class="abs dish-circle dish-pak" role="img" aria-label="Photo of Pakistani seekh kebab rolls"><span class="script">Pakistani Food</span></div>
    <div class="abs dish-circle dish-ind" role="img" aria-label="Photo of an Indian thali platter"><span class="script">Indian Food</span></div>
  </section>

  <!-- featured products -->
  <h2 class="abs section-title script products-title">Feature Products</h2>
  <div class="abs tab is-active" style="left:368px">Dinner</div>
  <div class="abs tab" style="left:488px">Breakfast</div>
  <div class="abs tab" style="left:607px">Meat</div>
  <div class="abs tab" style="left:727px">Beverages</div>

  <div class="abs product-photo photo-salad" role="img" aria-label="Photo of a Greek salad with feta, tomato and olives">
    <div class="abs cart-chip">
      <svg width="16" height="15" viewBox="0 0 16 15"><path d="M0 1h3l2 8h8l2-6H4.5" fill="none" stroke="#fff" stroke-width="2"/><circle cx="6" cy="12.5" r="1.5" fill="#fff"/><circle cx="12" cy="12.5" r="1.5" fill="#fff"/></svg>
    </div>
    <div class="abs price"><s>$ 120.00</s> $ 100.00</div>
  </div>
  <div class="abs product-photo photo-nacho" role="img" aria-label="Photo of loaded nachos with guacamole and sour cream"></div>
  <div class="abs product-photo photo-rice" role="img" aria-label="Photo of chicken biryani in a bowl"></div>

  <div class="abs product-name" style="left:120px">Finibus Bonorum et Malorum</div>
  <div class="abs product-name" style="left:453px">Finibus Bonorum et Malorum</div>
  <div class="abs product-name" style="left:785px">Finibus Bonorum et Malorum</div>
  <div class="abs stars" style="left:120px">★★★★★</div>
  <div class="abs stars" style="left:453px">★★★★★</div>
  <div class="abs stars" style="left:785px">★★★★★</div>

  <div class="abs pager" style="left:564px"><svg width="8" height="12" viewBox="0 0 8 12"><path d="M6 1L1 6l5 5" fill="none" stroke="#fff" stroke-width="2"/></svg></div>
  <div class="abs pager" style="left:606px"><svg width="8" height="12" viewBox="0 0 8 12"><path d="M2 1l5 5-5 5" fill="none" stroke="#fff" stroke-width="2"/></svg></div>

  <!-- footer -->
  <footer class="abs footer"></footer>
  <div class="abs footer-badge">Saffron<br>Lane</div>
  <div class="abs social" style="left:516px"></div>
  <div class="abs social" style="left:554px"></div>
  <div class="abs social" style="left:594px"></div>
  <div class="abs social" style="left:633px"></div>
  <div class="abs social" style="left:673px"></div>
  <div class="abs footer-links">Home &nbsp;/&nbsp; About us &nbsp;/&nbsp; Services &nbsp;/&nbsp; Contact us</div>
  <div class="abs footer-copy">Copyright @ 2016, Saffron Lane. All Rights Reserved.</div>

</div>
</body>
</html>
```